We are a local Communty Pharmacy wishing to promote and market a specialised Pharmaceutical Service

We would like a design that is professional and enticing ( according to the brief In attached files)
We wish to Market Compounding Pharmacy as a specialist side of our business.
We have the expertise a purpose built preparation laboratory.
The main purpose is an Internet presence that entices prospective patients to contact or visit our physical store.

Target Market(s)

Patients Medicos and Veterinary clients

Industry/Entity Type

Pharmacy

Coding

Coded - Design and coding required

Number of Pages Required

1 page

Requirements
Must have
• Clear friendly image
Nice to have
• soft enticing feel
Should not have
• No crass loud unprofessional elements

```html
<!DOCTYPE html>
<html lang="en">
<head>
<meta charset="utf-8">
<title>Wattlebrook Compounding Pharmacy</title>
<link href="https://fonts.googleapis.com/css2?family=Open+Sans:wght@400;600;700;800&display=swap" rel="stylesheet">
<style>
:root{
  --green:#5c9e3a;
  --blue:#1f5fa6;
  --navy:#1b4a86;
  --gold:#c9a133;
  --text:#555;
  --heading:#3a3a3a;
  --footer:#2a2c2e;
  --footer-text:#b9bcbf;
  --line:#e3e3e3;
}
*{box-sizing:border-box;margin:0;padding:0}
html,body{width:1200px;height:2172px;overflow:hidden}
body{font-family:"Open Sans",Arial,sans-serif;color:var(--text);background:#fff;position:relative}

.site-header{height:110px;display:flex;align-items:center;padding:0 40px 0 44px}
.brand{display:flex;align-items:center;gap:12px;width:430px}
.brand-mark{width:34px;height:34px;border-radius:50%;background:var(--blue)}
.brand-name{font-weight:800;font-size:24px;color:var(--navy)}
.header-address,.header-contact{display:flex;gap:10px;font-size:11px;line-height:17px;color:#666}
.header-address{width:420px}
.header-contact{flex-direction:column;gap:4px}
.header-contact div{display:flex;align-items:center;gap:8px}
.icon{flex:none}

.hero{position:relative;height:680px;overflow:hidden;
  background:
    radial-gradient(ellipse 300px 420px at 900px 520px,rgba(255,255,255,.95),rgba(255,255,255,0) 70%),
    radial-gradient(ellipse 180px 160px at 880px 170px,rgba(232,196,168,.75),rgba(232,196,168,0) 75%),
    radial-gradient(ellipse 200px 120px at 220px 110px,rgba(120,170,210,.55),rgba(120,170,210,0) 75%),
    radial-gradient(ellipse 220px 120px at 470px 470px,rgba(140,190,120,.45),rgba(140,190,120,0) 75%),
    radial-gradient(ellipse 200px 110px at 180px 560px,rgba(230,150,150,.35),rgba(230,150,150,0) 75%),
    radial-gradient(ellipse 180px 120px at 560px 150px,rgba(240,220,150,.45),rgba(240,220,150,0) 75%),
    linear-gradient(100deg,#e7eef3 0%,#f4f7f9 45%,#e2ebf0 70%,#cfdde6 100%)}
.hero-copy{position:absolute;left:40px;top:178px}
.hero-title{display:inline-block;font-size:44px;font-weight:800;color:var(--green);letter-spacing:.5px;line-height:52px;background:rgba(255,255,255,.7);padding:0 10px}
.hero-is{font-size:20px;font-weight:700;color:#444;margin:8px 0 4px 10px}
.hero-sub{font-size:20px;font-weight:700;color:#444;margin-left:10px}
.hero-arrow{position:absolute;top:300px;width:34px;height:34px;border-radius:50%;background:rgba(255,255,255,.8);display:flex;align-items:center;justify-content:center}
.hero-arrow.prev{left:14px}.hero-arrow.next{right:14px}

.about{padding:70px 40px 0;text-align:center}
.section-title{font-size:26px;font-weight:700;color:var(--green);letter-spacing:.5px}
.title-rule{width:120px;height:2px;background:var(--green);margin:14px auto 30px}
.about p{font-size:13px;line-height:22px;text-align:left;margin-bottom:20px}

.features{padding:70px 40px 0}
.features-head{display:flex;align-items:center;gap:16px;margin-bottom:28px}
.features-head h2{font-size:24px;font-weight:700;color:var(--green);white-space:nowrap}
.features-head span{flex:1;height:1px;background:var(--line)}
.feature-grid{display:flex;gap:52px}
.feature{width:356px}
.feature-media{height:226px;border:1px solid var(--line)}
.feature-media.vet{background:linear-gradient(135deg,#9cb7c8,#d9ccb6,#8d9aa2)}
.feature-media.scar{background:radial-gradient(circle at 50% 50%,#f0c8b4,#dfae98 45%,#c9d1da 80%)}
.feature-media.thyroid{background:linear-gradient(135deg,#bcd3e2,#e8eef2,#9fbcd0)}
.feature h3{font-size:16px;font-weight:700;color:var(--heading);margin:20px 0 8px}
.feature p{font-size:12px;line-height:19px;margin-bottom:18px;min-height:57px}
.btn{display:inline-block;background:var(--gold);color:#fff;font-size:11px;font-weight:600;padding:7px 16px;border-radius:2px}

.site-footer{position:absolute;left:0;top:1792px;width:1200px;height:316px;background:var(--footer);color:var(--footer-text);display:flex;padding:44px 40px 0}
.site-footer h4{color:#fff;font-size:15px;font-weight:700;margin-bottom:18px}
.hours{width:340px;font-size:12px;line-height:26px}
.hours .query{color:var(--gold);font-weight:600;margin-top:8px}
.map{width:420px;height:200px;background:linear-gradient(135deg,#e6e4dc,#d7dccf 50%,#e9e5da);margin:0 60px 0 0}
.contacts{font-size:12px;line-height:26px}
.contacts div{display:flex;gap:8px;align-items:center}

.bottom-bar{position:absolute;left:0;top:2108px;width:1200px;height:64px;background:var(--navy);display:flex;align-items:center;justify-content:space-between;padding:0 40px;color:#dfe8f3;font-size:12px}
.social{display:flex;align-items:center;gap:10px}
.social i{width:26px;height:26px;border-radius:50%;background:#4a8bd0;display:block}
</style>
</head>
<body>

<header class="site-header">
  <div class="brand"><span class="brand-mark"></span><span class="brand-name">Wattlebrook</span></div>
  <div class="header-address">
    <svg class="icon" width="16" height="20" viewBox="0 0 16 20"><path d="M8 0a7 7 0 0 0-7 7c0 5 7 13 7 13s7-8 7-13a7 7 0 0 0-7-7z" fill="#1f5fa6"/><circle cx="8" cy="7" r="2.6" fill="#fff"/></svg>
    <div>WATTLEBROOK COMMUNITY PHARMACY<br>SHOP 4, 22 WATTLE GROVE SHOPPING CENTRE<br>BROOKFIELD WA 6021</div>
  </div>
  <div class="header-contact">
    <div><svg class="icon" width="14" height="14" viewBox="0 0 14 14"><path d="M3 1l2 3-1.5 1.5a8 8 0 0 0 5 5L10 9l3 2-1.5 2.5C6 13 1 8 .5 2.5z" fill="#1f5fa6"/></svg>Phone (08) 9555 0142</div>
    <div><svg class="icon" width="14" height="14" viewBox="0 0 14 14"><rect x="1" y="4" width="12" height="8" fill="#1f5fa6"/><rect x="3" y="1" width="8" height="4" fill="#1f5fa6"/></svg>Fax (08) 9555 0143</div>
    <div><svg class="icon" width="14" height="14" viewBox="0 0 14 14"><rect x="1" y="3" width="12" height="9" fill="#1f5fa6"/><path d="M1 3l6 5 6-5" stroke="#fff" fill="none"/></svg>care@wattlebrookpharmacy.example</div>
  </div>
</header>

<section class="hero" role="img" aria-label="Friendly pharmacist in a white coat smiling in a bright pharmacy, shelves of colourful medicines behind him">
  <div class="hero-copy">
    <div class="hero-title">COMPOUNDING PHARMACY</div>
    <div class="hero-is">IS</div>
    <div class="hero-sub">CUSTOMISED MEDICATIONS FOR PATIENTS</div>
  </div>
  <span class="hero-arrow prev"><svg width="12" height="14" viewBox="0 0 12 14"><path d="M9 1L3 7l6 6" stroke="#666" stroke-width="2" fill="none"/></svg></span>
  <span class="hero-arrow next"><svg width="12" height="14" viewBox="0 0 12 14"><path d="M3 1l6 6-6 6" stroke="#666" stroke-width="2" fill="none"/></svg></span>
</section>

<section class="about">
  <h2 class="section-title">WHAT IS COMPOUNDING PHARMACY?</h2>
  <div class="title-rule"></div>
  <p>Not long ago, nearly every medicine was prepared by hand. A pharmacist would weigh, mix and measure each ingredient to suit the person in front of them. As large scale manufacturing took over during the last century, this skill faded from many community pharmacies, and most patients now receive the same standard strengths and forms as everyone else. Yet people are not all the same. Some cannot swallow tablets, some react to dyes, fillers or preservatives, and some need a dose that no manufacturer makes. Compounding brings back the craft of preparing a medicine for one person. Working closely with your doctor or vet, our trained pharmacists use quality ingredients and a purpose built laboratory to prepare creams, capsules, liquids, lozenges and more. Every preparation follows strict standards for accuracy, cleanliness and safety, and each one is checked before it leaves our hands, so you can be confident in what you take.</p>
  <p>We welcome scripts from doctors, dentists, specialists and veterinarians. Our compounding team holds current training and works to national practice guidelines. If you would like to know whether a medicine can be made to better suit you, your child or your animal, call us or visit the store and ask to speak with our compounding pharmacist.</p>
</section>

<section class="features">
  <div class="features-head"><h2>FEATURE ITEMS</h2><span></span></div>
  <div class="feature-grid">
    <article class="feature">
      <div class="feature-media vet" role="img" aria-label="Veterinarian examining a dog"></div>
      <h3>Vet Animals</h3>
      <p>Flavoured liquids, treats and transdermal gels make dosing easier for pets, with strengths suited to size and species.</p>
      <span class="btn">READ MORE</span>
    </article>
    <article class="feature">
      <div class="feature-media scar" role="img" aria-label="Close view of skin being treated for scarring"></div>
      <h3>Scar Therapy</h3>
      <p>Custom gels and creams prepared to soften, flatten and fade scars, made with ingredients chosen for your skin type.</p>
      <span class="btn">READ MORE</span>
    </article>
    <article class="feature">
      <div class="feature-media thyroid" role="img" aria-label="Doctor checking a patient's thyroid"></div>
      <h3>Thyroid Extract</h3>
      <p>Natural thyroid preparations made in exact strengths, as prescribed, for patients needing an unusual dose.</p>
      <span class="btn">READ MORE</span>
    </article>
  </div>
</section>

<footer class="site-footer">
  <div class="hours">
    <h4>Opening Hours</h4>
    <div>Monday – Friday: 8.30 am – 6.00 pm</div>
    <div>Saturday: 8.30 am – 1.00 pm</div>
    <div>Sunday: Closed</div>
    <div class="query">+ HAVE A QUERY</div>
  </div>
  <div class="map" role="img" aria-label="Street map showing the pharmacy location"></div>
  <div class="contacts">
    <h4>Contacts</h4>
    <div>Shop 4, 22 Wattle Grove, Brookfield WA 6021</div>
    <div>+ (08) 9555 0142</div>
    <div>care@wattlebrookpharmacy.example</div>
  </div>
</footer>

<div class="bottom-bar">
  <span>Copyright © Wattlebrook, 2015. All Rights Reserved.</span>
  <div class="social"><span>Social Networks</span><i></i><i></i><i></i><i></i></div>
</div>

</body>
</html>
```